New hardcover book cover

I want a striking, eye-catching cover with title, subtitle and a picture.See for previous book covers: www.brightquillpress.com

Target Market(s)

young, successful entrepreneurs that have built a business in a niche market that they discovered.

Font styles to use
Serif

Colors

Designer to choose colors to be used in the design.

Requirements
Must have
• A book cover that impresses and captures the imagination of those who look at it.
• MY MISTAKE, SORRY.
• Title: Founders Behind the Quiet Trade Boom
• Subtitle: 25 stories of success from
• discovering hidden opportunities
• Author: Dennis Harlow
• Please use the photo attached, thanks.

```html
<!DOCTYPE html>
<html lang="en">
<head>
<meta charset="utf-8">
<title>Founders Behind the Quiet Trade Boom — Book Cover</title>
<link rel="stylesheet" href="https://fonts.googleapis.com/css2?family=Marcellus&display=swap">
<style>
  :root {
    --stage: #2a2a2c;
    --ink-light: #ffffff;
    --ink-soft: #eef0f4;
    --target-red: #b8334f;
    --target-dark: #2d2936;
    --steel: #5e6a86;
    --sky: #a6c6e0;
    --shade: #1c1a22;
  }
  * { box-sizing: border-box; margin: 0; padding: 0; }
  html, body {
    width: 1200px; height: 905px; overflow: hidden;
    background: var(--stage);
  }
  .canvas {
    position: relative; width: 1200px; height: 905px;
    display: flex; align-items: center; justify-content: center;
  }
  .cover {
    position: relative; width: 540px; height: 860px; overflow: hidden;
    font-family: "Marcellus", serif; color: var(--ink-light);
    box-shadow: 0 20px 50px rgba(0,0,0,.5);
  }
  .cover-photo {
    position: absolute; inset: 0;
    background:
      linear-gradient(to bottom, rgba(28,26,34,.35) 0%, rgba(28,26,34,0) 20%, rgba(28,26,34,0) 50%, rgba(28,26,34,.8) 82%, var(--shade) 100%),
      linear-gradient(115deg, var(--target-red) 0%, #8a2d47 22%, var(--target-dark) 42%, var(--steel) 65%, var(--sky) 90%, #d6e4ef 100%);
  }
  .author {
    position: absolute; top: 62px; left: 0; right: 0;
    text-align: center; font-size: 32px;
    letter-spacing: 5px; text-transform: uppercase;
  }
  .title {
    position: absolute; top: 515px; left: 0; right: 0;
    text-align: center; font-weight: 400; text-transform: uppercase;
    line-height: 1;
  }
  .title-line { display: flex; align-items: center; justify-content: center; }
  .title-line--first { font-size: 42px; }
  .title-line--second { font-size: 52px; margin-top: 4px; }
  .title-line--third { font-size: 52px; margin-top: 6px; gap: 18px; }
  .title-line--fourth { font-size: 72px; margin-top: 6px; }
  .title-stack {
    display: flex; flex-direction: column; font-size: 16px;
    line-height: 1; margin-right: 10px; text-align: center;
  }
  .title-dash { display: inline-block; width: 44px; height: 5px; background: var(--ink-light); }
  .subtitle {
    position: absolute; top: 772px; left: 0; right: 0;
    text-align: center; font-size: 16px;
    line-height: 1.4; text-transform: uppercase; color: var(--ink-soft);
  }
</style>
</head>
<body>
  <main class="canvas">
    <article class="cover">
      <div class="cover-photo" role="img" aria-label="Photo: a dart striking the red centre of a dartboard against a blue sky"></div>
      <p class="author">Dennis Harlow</p>
      <h1 class="title">
        <span class="title-line title-line--first">Founders</span>
        <span class="title-line title-line--second"><span class="title-stack"><span>Behind</span><span>the</span></span>Quiet</span>
        <span class="title-line title-line--third"><span class="title-dash"></span>Trade<span class="title-dash"></span></span>
        <span class="title-line title-line--fourth">Boom</span>
      </h1>
      <p class="subtitle">25 captivating stories of success<br>from discovering hidden opportunities</p>
    </article>
  </main>
</body>
</html>
```